Sleek wordpress site for Bramblecrest finishing works

We are a commercial job shop that serves B2B, govt & LEO and retail clients.We need a wordpress site with 6 individual pages: homepage, coating, laser engraving, laser cutting, part marking, and contact us. I have attached an outline of the desired flow and sub headings for each page. I would like to incorporate the colors of the logo through out the site to be clean and sleek enough to appeal to B2B commercial clients yet be inviting enough for retail clients.

I would like to have easy picture functionality so photographs on each page can be updated easily.

Target Market(s)

B2B industrial & Govt and Military part marking, laser engraving and coating: machine shops, aerospace companies, tool manufactures. Retail: personalized gifts, Job Shop

Coding

Coded - Design and coding required

Font styles to use
Sans Serif
Other font styles liked:
• Open to suggestion

Colors
0255a3
3176b5
eaf1f7
cfdeed
ffffff

Requirements
Must have
• Clean easy to navigate flow, separate pages as indicated on attached outline, high class feel. Great picture functionality, professional and inviting feel,
• **update: needs to be optimized for mobile, should have a gallery function. Gallery can be an additional page or embedded
Nice to have
• Social media connectivity links,
Should not have
• crappy plugins that make back-end management difficult, no blog

```html
<!DOCTYPE html>
<html lang="en">
<head>
<meta charset="utf-8">
<title>Bramblecrest Finishing Works</title>
<link href="https://fonts.googleapis.com/css2?family=Roboto:wght@500;700&family=Poppins:wght@500;600&family=Lato:wght@400;700&display=swap" rel="stylesheet">
<style>
  :root{
    --brand:#0255a3;
    --brand-mid:#3176b5;
    --tint:#eaf1f7;
    --tint-2:#cfdeed;
    --white:#ffffff;
    --ink:#555a60;
    --dark:#140f0c;
    --rule:rgba(255,255,255,.45);
  }
  *{box-sizing:border-box;margin:0;padding:0}
  html,body{width:691px;height:1200px;overflow:hidden;background:var(--white)}
  body{position:relative;font-family:"Lato",sans-serif;color:var(--ink)}
  a{color:inherit;text-decoration:none}

  /* Hero */
  .hero{position:absolute;left:0;top:0;width:691px;height:348px;
    background:radial-gradient(circle at 290px 165px,#fff8e8 0,#f0c878 40px,#a8702e 95px,#4a2e17 180px,#1a120d 320px,#0c0a09 100%)}
  .site-header{position:absolute;left:0;top:0;width:100%;height:70px}
  .brand-name{position:absolute;left:44px;top:22px;width:100px;color:var(--white);
    font:700 10px/1.25 "Lato",sans-serif;text-transform:uppercase;letter-spacing:.3px}
  .main-nav{position:absolute;left:228px;top:29px;display:flex;gap:22px;
    font:700 9px "Lato",sans-serif;color:var(--white)}
  .cart{position:absolute;left:632px;top:28px}
  .hero-title{position:absolute;left:45px;top:136px;color:var(--white);
    font:700 18.5px/1.32 "Roboto",sans-serif;text-transform:uppercase}
  .hero-text{position:absolute;left:45px;top:196px;width:210px;color:var(--white);
    font:400 8.8px/1.7 "Lato",sans-serif}
  .btn-outline{position:absolute;display:flex;align-items:center;justify-content:center;
    width:84px;height:30px;border:1px solid var(--white);border-radius:4px;color:var(--white);
    font:500 10px "Poppins",sans-serif}
  .hero .btn-outline{left:45px;top:246px}

  /* Services */
  .services{position:absolute;left:0;top:348px;width:691px;height:192px}
  .service{position:absolute;top:36px;width:140px;text-align:center}
  .service-icon{display:block;margin:0 auto;width:42px;height:42px;border-radius:3px;
    background:var(--brand);box-shadow:2px 3px 4px rgba(0,0,0,.3)}
  .service h3{margin-top:21px;color:var(--brand);font:600 10.5px "Poppins",sans-serif}
  .service p{margin-top:5px;font:400 8.6px/1.75 "Lato",sans-serif;color:#666}
  .service p a{color:var(--brand);text-decoration:underline;font-weight:700}

  /* Contact */
  .contact{position:absolute;left:0;top:540px;width:691px;height:287px;
    background:linear-gradient(90deg,#2a1c12 0,#6b4320 30%,#3b2716 48%,#3b2716 100%)}
  .contact-photo{position:absolute;left:0;top:0;width:329px;height:287px;
    background:radial-gradient(circle at 130px 150px,#f7d9a0 0,#c47a2c 60px,#5a3a1c 140px,#221710 100%)}
  .contact-photo-edge{position:absolute;left:646px;top:0;width:45px;height:287px;
    background:linear-gradient(180deg,#6a4422,#2c2119 60%,#5a4a3c)}
  .contact-panel{position:absolute;left:329px;top:0;width:317px;height:287px;background:var(--brand)}
  .contact-panel h2{position:absolute;left:25px;top:34px;color:var(--white);font:700 18px "Roboto",sans-serif}
  .field{position:absolute;left:23px;width:240px;border-bottom:1px solid var(--rule);
    color:var(--white);font:400 8.8px "Lato",sans-serif;padding-left:7px}
  .contact-panel .btn-outline{left:23px;top:222px}

  /* Newsletter */
  .newsletter{position:absolute;left:0;top:827px;width:691px;height:186px;text-align:center}
  .newsletter h2{margin-top:37px;color:var(--brand);font:700 18px "Roboto",sans-serif}
  .newsletter p{margin-top:10px;font:400 8.8px/1.7 "Lato",sans-serif;color:#666}
  .input{position:absolute;top:120px;height:31px;border:1px solid #dcdcdc;border-radius:4px;
    box-shadow:0 0 3px rgba(0,0,0,.12);text-align:left;padding:9px 7px;font:400 8.6px "Lato",sans-serif;color:#777}
  .btn-solid{position:absolute;left:479px;top:121px;width:83px;height:29px;border-radius:3px;
    background:var(--brand);color:var(--white);display:flex;align-items:center;justify-content:center;
    font:600 10.5px "Poppins",sans-serif}

  /* Footer */
  .site-footer{position:absolute;left:0;top:1013px;width:691px;height:187px;background:var(--brand);color:var(--white)}
  .footer-brand{position:absolute;left:0;top:22px;width:100%;text-align:center;
    font:700 10px/1.3 "Lato",sans-serif;text-transform:uppercase;letter-spacing:.3px}
  .footer-nav{position:absolute;left:0;top:85px;width:100%;display:flex;justify-content:center;gap:14px;
    font:400 8.8px "Lato",sans-serif}
  .footer-nav .sep{opacity:.9}
  .social{position:absolute;left:298px;top:114px;display:flex;gap:4px}
  .social span{width:20px;height:20px;border-radius:50%;background:var(--brand-mid)}
  .footer-rule{position:absolute;left:45px;top:151px;width:601px;border-top:1px solid rgba(255,255,255,.25)}
  .copyright{position:absolute;left:0;top:163px;width:100%;text-align:center;font:400 8.6px "Lato",sans-serif}
  .copyright b{font-weight:700}
</style>
</head>
<body>

<section class="hero" role="img" aria-label="Laser cutting head sending sparks across an engraved metal plate">
  <header class="site-header">
    <div class="brand-name">Bramblecrest finishing works</div>
    <nav class="main-nav">
      <a href="#">Home</a><a href="#">Coating</a><a href="#">Laser Engraving</a>
      <a href="#">Laser Cutting</a><a href="#">Part Marketing</a><a href="#">Contact Us</a>
    </nav>
    <svg class="cart" width="15" height="14" viewBox="0 0 15 14" fill="none" stroke="#fff" stroke-width="1.3">
      <path d="M1 5h13l-1.6 7.5H2.6z"/><path d="M4 5l3-4M11 5L8 1"/><path d="M5.5 7v4M7.5 7v4M9.5 7v4"/>
    </svg>
  </header>
  <h1 class="hero-title">Bramblecrest<br>finishing works</h1>
  <p class="hero-text">Lorem Ipsum is simply dummy text of the printing and typesetting industry.</p>
  <a class="btn-outline" href="#">Contact Us</a>
</section>

<section class="services">
  <div class="service" style="left:42px">
    <svg class="service-icon" viewBox="0 0 42 42" fill="none" stroke="#fff" stroke-width="1.5">
      <rect x="17" y="12" width="12" height="7" rx="1"/><path d="M23 19v6M20 25h6M23 25v5"/><path d="M12 15h3M11 12h2M11 18h2"/>
    </svg>
    <h3>Coating</h3>
    <p>Duraglaze is a spray on ceramic based finish that can be applied to metals,....<a href="#">Read More</a></p>
  </div>
  <div class="service" style="left:197px">
    <svg class="service-icon" viewBox="0 0 42 42" fill="none" stroke="#fff" stroke-width="1.5">
      <path d="M13 11h16M16 11l5 8 5-8"/><path d="M21 19v8M17 25l-3 3M25 25l3 3"/><path d="M12 30h18"/>
    </svg>
    <h3>Laser engraving</h3>
    <p>Capabilities Statement: With our selection of CO2 and fiber lasers there are very.....<a href="#">Read More</a></p>
  </div>
  <div class="service" style="left:353px">
    <svg class="service-icon" viewBox="0 0 42 42" fill="none" stroke="#fff" stroke-width="1.5">
      <path d="M18 9h6l-1 10h-4z" fill="#fff"/><path d="M21 21v7M17 29h8M14 32h14"/>
    </svg>
    <h3>Laser Cutting</h3>
    <p>What is laser cutting: Laser cutting is a non-contact cutting process with....<a href="#">Read More</a></p>
  </div>
  <div class="service" style="left:509px">
    <svg class="service-icon" viewBox="0 0 42 42" fill="none" stroke="#fff" stroke-width="1.5">
      <path d="M27 11l4 4-14 14-5 1 1-5z"/><path d="M24 14l4 4M15 25l2 2"/>
    </svg>
    <h3>Part Marking</h3>
    <p>o&nbsp; Picture slider<br>o&nbsp; Capabilities<br>Barcodes ....<a href="#">Read More</a></p>
  </div>
</section>

<section class="contact">
  <div class="contact-photo" role="img" aria-label="Cutting torch throwing sparks off a steel workpiece"></div>
  <form class="contact-panel">
    <h2>Contact Us</h2>
    <div class="field" style="top:68px;height:28px">Name*</div>
    <div class="field" style="top:98px;height:28px">E-mail*</div>
    <div class="field" style="top:128px;height:28px">Phone*</div>
    <div class="field" style="top:158px;height:58px">Message</div>
    <a class="btn-outline" href="#">Send Now!</a>
  </form>
  <div class="contact-photo-edge" role="img" aria-label="Workshop sparks detail"></div>
</section>

<section class="newsletter">
  <h2>Newsletter</h2>
  <p>Lorem Ipsum is simply dummy text of the printing and typesetting industry.<br>Lorem Ipsum has been the industry's</p>
  <div class="input" style="left:130px;width:169px">Name*</div>
  <div class="input" style="left:304px;width:169px">E-mail*</div>
  <a class="btn-solid" href="#">Subscribe</a>
</section>

<footer class="site-footer">
  <div class="footer-brand">Bramblecrest<br>finishing works</div>
  <nav class="footer-nav">
    <a href="#">Home</a><span class="sep">|</span><a href="#">Coating</a><span class="sep">|</span>
    <a href="#">Laser Engraving</a><span class="sep">|</span><a href="#">Laser Cutting</a><span class="sep">|</span>
    <a href="#">Part Markeing</a><span class="sep">|</span><a href="#">Contact Us</a>
  </nav>
  <div class="social"><span></span><span></span><span></span><span></span></div>
  <div class="footer-rule"></div>
  <p class="copyright"><b>© BRAMBLECREST FINISHING WORKS - 2018.</b> All Rights Reserved.</p>
</footer>

</body>
</html>
```